Business Card Design (NEW FILES)

ATTENTION: New vector files are available. Please update your design to reflect/use the new (better resolution) logo images.

Seeking a unique and professional business card design for a commercial drone photography/videography business. The layout should feature
the logo (attached) and include the following information:
Owen Tarrick
614-502-7738
www.skylarkreelworks.example
NRD Certified Remote Pilot

Owen Tarrick

```html
<!DOCTYPE html>
<html lang="en">
<head>
<meta charset="utf-8">
<title>Skylark Reelworks — Business Card</title>
<link href="https://fonts.googleapis.com/css2?family=Arimo:ital,wght@0,400;0,700;1,400&display=swap" rel="stylesheet">
<style>
  :root{
    --stage:#161616;
    --card:#ffffff;
    --navy:#0f1440;
    --orange:#ec8a4a;
    --ink-light:#ffffff;
  }
  html,body{margin:0;padding:0;width:1200px;height:963px;overflow:hidden;background:var(--stage);}
  .business-card{
    position:absolute;left:100px;top:195px;width:1000px;height:572px;
    background:var(--card);border-radius:36px;overflow:hidden;
    font-family:"Arimo",Arial,sans-serif;
  }
  .wave-art{position:absolute;inset:0;width:100%;height:100%;}
  .owner-block{position:absolute;left:60px;top:48px;}
  .owner-name{margin:0;font-size:34px;font-weight:700;letter-spacing:1px;color:var(--navy);text-transform:uppercase;}
  .owner-name .surname{color:var(--orange);}
  .owner-title{margin:4px 0 0;font-size:22px;color:var(--navy);}
  .credentials{position:absolute;left:60px;top:345px;color:var(--ink-light);}
  .credentials p{margin:0 0 10px;font-size:24px;font-style:italic;}
  .contact-list{position:absolute;left:60px;top:440px;list-style:none;margin:0;padding:0;color:var(--ink-light);}
  .contact-list li{display:flex;align-items:center;gap:14px;font-size:24px;font-style:italic;margin-bottom:14px;}
  .contact-list svg{width:22px;height:22px;flex:none;}
  .brand-mark{position:absolute;left:560px;top:225px;display:flex;align-items:center;gap:18px;}
  .brand-name{margin:0;font-size:44px;font-weight:700;line-height:1.05;color:var(--navy);text-transform:uppercase;letter-spacing:2px;}
  .brand-dot{width:38px;height:38px;border-radius:50%;background:var(--orange);flex:none;}
</style>
</head>
<body>
  <div class="business-card">
    <svg class="wave-art" viewBox="0 0 1000 572" preserveAspectRatio="none" aria-hidden="true">
      <path d="M0,205 C190,185 300,235 385,380 C445,485 525,560 620,572 L0,572 Z" fill="var(--navy)"/>
      <path d="M395,370 C460,470 530,545 620,566" fill="none" stroke="var(--navy)" stroke-width="5"/>
      <path d="M0,175 C170,150 285,190 350,250" fill="none" stroke="var(--orange)" stroke-width="9" stroke-linecap="round"/>
      <path d="M520,470 C610,535 740,562 880,556" fill="none" stroke="var(--orange)" stroke-width="8" stroke-linecap="round"/>
    </svg>

    <div class="owner-block">
      <h1 class="owner-name">Owen <span class="surname">Tarrick</span></h1>
      <p class="owner-title">Owner</p>
    </div>

    <div class="brand-mark">
      <h2 class="brand-name">Skylark<br>Reelworks</h2>
      <span class="brand-dot"></span>
    </div>

    <div class="credentials">
      <p>NRD Certified Remote Pilot</p>
      <p>Fully Insured</p>
    </div>

    <ul class="contact-list">
      <li>
        <svg viewBox="0 0 24 24"><path d="M6.6 10.8a15 15 0 0 0 6.6 6.6l2.2-2.2a1 1 0 0 1 1-.25 11 11 0 0 0 3.6.6 1 1 0 0 1 1 1V20a1 1 0 0 1-1 1A17 17 0 0 1 3 4a1 1 0 0 1 1-1h3.5a1 1 0 0 1 1 1 11 11 0 0 0 .6 3.6 1 1 0 0 1-.25 1z" fill="var(--orange)"/></svg>
        614-502-7738
      </li>
      <li>
        <svg viewBox="0 0 24 24" fill="none" stroke="var(--orange)" stroke-width="1.8"><circle cx="12" cy="12" r="9"/><ellipse cx="12" cy="12" rx="4" ry="9"/><path d="M3 12h18M5 7h14M5 17h14"/></svg>
        www.skylarkreelworks.example
      </li>
    </ul>
  </div>
</body>
</html>
```